A website where experts collaborate on your project

I am building a new website where experts (yes, like designers) collaborate on projects with the project owner. More minds = more collaboration = better end product. Please see Pelmora(dot)com for a quick landing page I created for collaborating on presentations (although there will be many project types offered)

I am looking for a DESIGNER LONG TERM, but for now, just need initial mock ups to show the web programmers.

I have 21 Word documents loosely designed, what I would like to see here is a theme. Please DO NOT GO OFF WHAT YOU CURRENTLY SEE AT PELMORA. What is up now is only a quick landing page.

You can view a Word doc of the homepage here:
https://www.filevanta.com/s/qx83kdm2/home.docx?dl=0

WHAT AM I LOOKING FOR?
A clean, well designed theme.

Here is a link to the logo:
https://www.filevanta.com/s/mr47tpz9/logo%20-%20horizontal.tif?dl=0
-----------------------------------------
Here are a few sites I like the design of and what I like about them:
www.quenbrook.com-all around my favorite, beautiful graphics, clean layout, bold use of colors on a dark background
Ravelto.com- clean layout, The use of humans and bubble style elements.
Mintharbor.com :) clean, bold, unique pop art style but professional
plumevault.com - From the unique colors and artwork and the ability of that art to not interfere with the important elements of the site
sparkwidgets.com-clean, nice colors, well organized and separated sections.
www.dunmereco.com-love the font, use of colors and sectionalized style

All in all, I am not picky and open to so many styles. I would ultimately like the designer I pick to design all 21 pages.
Updates

Hello everyone,Moving forward, I would like you all to pay special attention to the section in my brief titled "Here are a few sites I like the design of and what I like about them". Please see below, I handpicked each one of these as sites I really like. Thank you.Here are a few sites I like the design of and what I like about them:Ravelto.com- clean layout, The use of humans and bubble style elements.Mintharbor.com :) clean, bold, unique pop art style but professionalwriteraccess.com - From the unique colors and artwork and the ability of that art to not interfere with the important elements of the sitegrowthgeeks.com-clean, nice colors, well organized and separated sections.www.dunmereco.com-love the font, use of colors and sectionalized stylewww.quenbrook.com-beautiful graphics, clean layout, bold use of colors----------------------------------------- Added Tuesday, November 24, 2015

I updated the homepage, you can see it here:https://www.dropbox.com/s/kwlkbsookq3cg2m/1new%20homepage.docx?dl=0I am modeling it after my favorite designed site: triplelift.comI love the dark colors with the orange glowing style boldness of the buttons. It's real clean too. Added Tuesday, November 24, 2015

Target Market(s)

small business owners, marketers, freelancer writers, graphic designers,

Industry/Entity Type

Building

Number of Pages Required

5+ page

Requirements
Must have
• I can't think of anything the project must have.
Nice to have
• WHAT AM I LOOKING FOR?
• A clean, well designed theme. I had a designer do a bit of work putting elements together, I found it to be very plain, but I like the Application Page (https://www.filevanta.com/s/jb19ckr3/Pelmora-Website.ai?dl=0)
• Here is a link to the logo:
• https://www.filevanta.com/s/mr47tpz9/logo%20-%20horizontal.tif?dl=0
• Here are a few sites I like the design of and what I like about them:
• Ravelto.com- clean layout, The use of humans and bubble style elements.
• Mintharbor.com :) clean, bold, unique pop art style but professional
• plumevault.com - From the unique colors and artwork and the ability of that art to not interfere with the important elements of the site
• sparkwidgets.com-clean, nice colors, well organized and separated sections.
• www.dunmereco.com-love the font, use of colors and sectionalized style
• www.quenbrook.com-beautiful graphics, clean layout, bold use of colors
• -----------------------------------------
Should not have
• out of the boxed, templated style website. I want this site to be memorable and not look like a thousand others

```html
<!DOCTYPE html>
<html lang="en">
<head>
<meta charset="utf-8">
<title>Pelmora – Convert more customers</title>
<link href="https://fonts.googleapis.com/css2?family=Open+Sans:ital,wght@0,400;0,600;0,700;1,400;1,600&display=swap" rel="stylesheet">
<style>
:root{
  --brand-orange:#f07d1e;
  --sky:#5bb7d5;
  --sky-dark:#3e9fc1;
  --ink:#333;
  --muted:#777;
  --paper:#fff;
  --mist:#e8e9ea;
  --night:#111;
}
*{box-sizing:border-box;margin:0;padding:0}
html,body{width:855px;height:1200px;overflow:hidden;background:var(--paper)}
body{font-family:"Open Sans",Arial,sans-serif;color:var(--ink)}
.page{position:relative;width:855px;height:1200px;overflow:hidden}

/* header */
.site-header{position:absolute;left:0;top:0;width:855px;height:80px;background:var(--paper);border-bottom:1px solid #ddd}
.brand{position:absolute;left:88px;top:27px;color:var(--ink);font-weight:600;font-size:20px}
.search{position:absolute;left:285px;top:28px;width:145px;height:24px;border:1px solid #ccc;border-radius:3px;font-size:11px;color:#999;padding:4px 8px 0 22px}
.search svg{position:absolute;left:6px;top:6px}
.main-nav{position:absolute;left:452px;top:32px;display:flex;gap:16px;font-size:13px;color:#222}
.main-nav .active{color:var(--brand-orange)}

/* hero */
.hero{position:absolute;left:0;top:80px;width:855px;height:305px;background:var(--sky)}
.hero h1{position:absolute;left:88px;top:42px;color:#fff;font-weight:400;font-size:34px}
.hero p{position:absolute;left:88px;top:102px;width:275px;color:#fff;font-size:21px;line-height:26px}
.btn-outline{position:absolute;border:1.5px solid #fff;color:#fff;font-size:11px;font-weight:600;letter-spacing:.5px;text-align:center;text-transform:uppercase}
.hero .btn-outline{left:88px;top:210px;width:160px;height:34px;line-height:31px}
.hero-figure{position:absolute;left:545px;top:22px;width:130px;height:283px;background:linear-gradient(180deg,#f5a55a 0%,#e6e9ec 45%,#2f3a44 100%);border-radius:65px 65px 0 0;opacity:.9}

/* projects */
.browse{position:absolute;left:0;top:385px;width:855px;height:427px;background:var(--mist)}
.filters{position:absolute;left:57px;top:38px;width:285px;height:372px;background:var(--sky);color:#fff;padding:30px 30px 0 35px;font-size:12px}
.filters h2{font-size:13px;font-weight:600;margin-bottom:10px}
.filter-list{list-style:none}
.filter-list li{line-height:22px}
.price{display:flex;align-items:center;gap:10px}
.slider{position:relative;flex:1;height:2px;background:#fff}
.slider::after{content:"";position:absolute;left:58%;top:-5px;width:12px;height:12px;border-radius:50%;background:#fff}
.filters .btn-outline{left:35px;bottom:26px;width:115px;height:30px;line-height:27px}
.projects{position:absolute;left:342px;top:38px;width:458px;height:340px;background:var(--paper);padding:22px 20px 0 32px}
.projects-head{display:flex;justify-content:space-between;align-items:center;font-size:12px}
.projects-head h2{font-size:13px;font-weight:600;border-bottom:2px solid var(--sky);padding-bottom:4px}
.sort{display:flex;gap:12px;align-items:center;color:var(--muted);font-size:11px}
.sort span{display:flex;align-items:center;gap:3px}
.project-list{list-style:none;margin-top:16px}
.project{padding:6px 8px;font-size:11px;line-height:15px;margin-bottom:4px}
.project.highlight{border:1.5px solid var(--sky);margin-left:-8px}
.project-title{color:var(--sky-dark)}
.project-meta b{font-weight:700}
.featured{color:var(--brand-orange);font-size:10px}
.projects .see-all{display:inline-block;margin:6px 0 0 8px;border:1px solid #555;font-size:10px;font-weight:600;padding:5px 10px}

/* testimonial */
.testimonial{position:absolute;left:0;top:812px;width:855px;height:278px;background:var(--paper);text-align:center}
.testimonial blockquote{position:absolute;left:170px;top:75px;width:515px;font-style:italic;color:var(--muted);font-size:17px;line-height:24px}
.testimonial blockquote::before{content:"\201C";color:var(--sky);font-size:44px;font-style:normal;position:absolute;left:-10px;top:-8px}
.testimonial blockquote::after{content:"\201D";color:var(--sky);font-size:44px;font-style:normal;position:absolute;right:-8px;bottom:-20px}
.author{position:absolute;left:0;right:170px;top:140px;text-align:right;font-size:14px;color:var(--ink)}
.author b{font-weight:700}
.dots{position:absolute;left:407px;top:205px;display:flex;gap:5px}
.dots i{width:10px;height:10px;border-radius:50%;background:var(--sky)}
.dots i.current{background:#2c3e4c}

/* footer */
.site-footer{position:absolute;left:0;top:1090px;width:855px;height:110px;background:var(--night);color:#eee;text-align:center;font-size:13px;font-style:italic;font-weight:600;padding-top:62px}
</style>
</head>
<body>
<div class="page">
  <header class="site-header">
    <div class="brand">Pelmora</div>
    <div class="search">
      <svg width="10" height="10" viewBox="0 0 10 10"><circle cx="4" cy="4" r="3" fill="none" stroke="#999" stroke-width="1.3"/><line x1="6.3" y1="6.3" x2="9" y2="9" stroke="#999" stroke-width="1.3"/></svg>
      Search Project
    </div>
    <nav class="main-nav">
      <span class="active">Home</span><span>Projects</span><span>How it Works</span><span>Plans</span><span>My Account</span>
    </nav>
  </header>

  <section class="hero">
    <h1>Convert more customers</h1>
    <p>Experience the power of experts collaborating on your project.</p>
    <span class="btn-outline">Get started</span>
    <div class="hero-figure" role="img" aria-label="Illustrated businessman standing with hands in pockets"></div>
  </section>

  <section class="browse">
    <aside class="filters">
      <h2>Filters</h2>
      <ul class="filter-list">
        <li class="price">Price List <span class="slider"></span> $1,000+</li>
        <li>Country</li>
        <li>Categories</li>
        <li>Time Left</li>
        <li>Active / Expired</li>
        <li>Contains adult content</li>
        <li>Keywords</li>
        <li>Followers</li>
        <li>+ more</li>
      </ul>
      <span class="btn-outline">Save filter</span>
    </aside>

    <div class="projects">
      <div class="projects-head">
        <h2>Crowd Projects</h2>
        <div class="sort">Sort:
          <span><svg width="11" height="11" viewBox="0 0 11 11"><circle cx="5.5" cy="5.5" r="4.5" fill="none" stroke="#777"/></svg>Price</span>
          <span><svg width="11" height="11" viewBox="0 0 11 11"><circle cx="5.5" cy="5.5" r="4.5" fill="none" stroke="#777"/><path d="M1 5.5h9M5.5 1v9" stroke="#777"/></svg>Country</span>
          <span><svg width="11" height="11" viewBox="0 0 11 11"><circle cx="5.5" cy="5.5" r="4.5" fill="none" stroke="#777"/><path d="M5.5 3v3h2" stroke="#777" fill="none"/></svg>Time left</span>
        </div>
      </div>
      <ul class="project-list">
        <li class="project highlight"><div class="project-title">Mordo in ante arcu. Maecenas sit amet sem vel</div><div class="project-meta"><b>$80</b>, U.K., time left 6 days</div></li>
        <li class="project"><div class="project-title">Lorem ipsum dolor sit amet, consectetur adipiscing</div><div class="project-meta"><b>$90</b>, CA, time left 6 days</div><div class="featured">Featured</div></li>
        <li class="project"><div class="project-title">Neque porro quisquam est qui dolorem ipsum</div><div class="project-meta"><b>$250</b>, U.S., time left 6 days</div></li>
        <li class="project"><div class="project-title">Duis ligula sapien, sodales id tortor vitae, ornare</div><div class="project-meta"><b>$62</b>, U.K., time left 6 days</div></li>
        <li class="project"><div class="project-title">Neque porro quisquam est qui dolorem ipsum</div><div class="project-meta"><b>$48</b>, U.S., time left 6 days</div></li>
      </ul>
      <span class="see-all">SEE ALL</span>
    </div>
  </section>

  <section class="testimonial">
    <blockquote>With Pelmora I have multiple experts perfecting my content and I only pay for the feedback I find valuable. It's perfect</blockquote>
    <p class="author"><b>Dana Whitlow</b>, CEO, Ferro 41</p>
    <div class="dots"><i></i><i class="current"></i><i></i></div>
  </section>

  <footer class="site-footer">Media Logos | Media Logos | Media Logos</footer>
</div>
</body>
</html>
```